Harbourline Electrical Solutions

On one side. LOGO (underneath:) Commercial Industrial Residential

- NAME & CONTACT DETAILS

Marcus T. Hollings
Project Manager

(Cell icon) (441) 555-0187
(Email icon) hlelectricalsolutions@mailvento.com
(Facebook & Instagram icons )@hlelectricalsolutions

Other side: LOGO - underneath ELECTRICAL CONSTRUCTION & MAINTENANCE . LED LIGHTING & AUTOMATION . LIFE SAFETY SYSTEMS (FIRE ALARM / SECURITY) . DATA & COMMUNICATION

```html
<!DOCTYPE html>
<html lang="en">
<head>
<meta charset="utf-8">
<title>Harbourline Electrical Solutions – Business Card</title>
<link rel="stylesheet" href="https://fonts.googleapis.com/css2?family=Montserrat:wght@500;600&family=Arimo:wght@400;700&display=swap">
<style>
  :root {
    --bg: #2b2b2b;
    --card: #111111;
    --teal: #1a5a74;
    --white: #ffffff;
  }
  * { margin: 0; padding: 0; box-sizing: border-box; }
  html, body { width: 1200px; height: 1000px; overflow: hidden; }
  body {
    background: var(--bg);
    display: flex;
    flex-direction: column;
    align-items: center;
    justify-content: center;
    gap: 40px;
    font-family: "Arimo", Arial, sans-serif;
    color: var(--white);
  }
  .card {
    position: relative;
    width: 760px;
    height: 434px;
    background: var(--card);
    box-shadow: 0 10px 30px rgba(0,0,0,.5);
    overflow: hidden;
  }
  .card__band {
    position: absolute;
    left: 0; right: 0;
    height: 12px;
    background: var(--teal);
  }
  .brand {
    position: absolute;
    display: flex;
    align-items: center;
    gap: 18px;
  }
  .brand__dot {
    width: 62px; height: 62px;
    border-radius: 50%;
    background: var(--teal);
  }
  .brand__rule {
    width: 3px; height: 84px;
    background: var(--white);
  }
  .brand__name {
    font-family: "Montserrat", sans-serif;
    font-weight: 600;
    font-size: 22px;
    line-height: 1.05;
    letter-spacing: 4px;
    text-transform: uppercase;
    color: var(--white);
  }
  /* services side */
  .card--services .brand { left: 200px; top: 110px; }
  .card--services .card__band { bottom: 70px; }
  .services {
    position: absolute;
    left: 70px; right: 40px; top: 230px;
    display: grid;
    grid-template-columns: 1.25fr 1fr;
    row-gap: 14px;
    column-gap: 20px;
    list-style: none;
    font-family: "Montserrat", sans-serif;
    font-weight: 500;
    font-size: 12.5px;
    letter-spacing: .5px;
    text-transform: uppercase;
  }
  .services li { display: flex; align-items: center; gap: 9px; }
  .services li::before {
    content: "";
    width: 6px; height: 6px;
    border: 1px solid var(--teal);
    border-radius: 50%;
    flex: none;
  }
  /* contact side */
  .card--contact .brand { right: 70px; top: 60px; }
  .card--contact .brand__dot { width: 54px; height: 54px; }
  .card--contact .brand__rule { height: 74px; }
  .card--contact .brand__name { font-size: 19px; }
  .card--contact .card__band { bottom: 0; }
  .person { position: absolute; left: 60px; top: 190px; }
  .person__name {
    font-weight: 700;
    font-size: 30px;
    letter-spacing: 1px;
    color: var(--teal);
    text-transform: uppercase;
  }
  .person__role { font-size: 18px; margin-top: 4px; }
  .card__divider {
    position: absolute;
    left: 60px; right: 60px; top: 272px;
    height: 1.5px;
    background: var(--teal);
  }
  .contacts {
    position: absolute;
    left: 60px; top: 296px;
    list-style: none;
    font-size: 17px;
  }
  .contacts li { display: flex; align-items: center; gap: 12px; margin-bottom: 12px; }
  .icon {
    width: 26px; height: 26px;
    border-radius: 50%;
    background: var(--teal);
    display: flex; align-items: center; justify-content: center;
    flex: none;
  }
  .social {
    position: absolute;
    right: 60px; bottom: 40px;
    display: flex; align-items: center; gap: 8px;
    font-size: 18px;
  }
  .social__mark {
    width: 24px; height: 24px;
    border-radius: 50%;
    background: var(--teal);
  }
  .social__handle { margin-left: 6px; }
</style>
</head>
<body>

  <section class="card card--services" aria-label="Services side">
    <div class="brand">
      <span class="brand__dot"></span>
      <span class="brand__rule"></span>
      <span class="brand__name">Harbourline<br>Electrical<br>Solutions</span>
    </div>
    <ul class="services">
      <li>Electrical Construction &amp; Maintenance</li>
      <li>LED Lighting &amp; Automation</li>
      <li>Life Safety Systems (Fire Alarm / Security)</li>
      <li>Data &amp; Communication</li>
    </ul>
    <div class="card__band"></div>
  </section>

  <section class="card card--contact" aria-label="Contact side">
    <div class="brand">
      <span class="brand__dot"></span>
      <span class="brand__rule"></span>
      <span class="brand__name">Harbourline<br>Electrical<br>Solutions</span>
    </div>
    <div class="person">
      <h1 class="person__name">Marcus T. Hollings</h1>
      <p class="person__role">Project Manager</p>
    </div>
    <div class="card__divider"></div>
    <ul class="contacts">
      <li>
        <span class="icon">
          <svg width="14" height="14" viewBox="0 0 24 24" aria-hidden="true"><path fill="#fff" d="M6.6 10.8a15.1 15.1 0 0 0 6.6 6.6l2.2-2.2a1 1 0 0 1 1-.25 11.4 11.4 0 0 0 3.6.57 1 1 0 0 1 1 1V20a1 1 0 0 1-1 1A17 17 0 0 1 3 4a1 1 0 0 1 1-1h3.5a1 1 0 0 1 1 1c0 1.25.2 2.45.57 3.57a1 1 0 0 1-.25 1z"/></svg>
        </span>
        (441) 555-0187
      </li>
      <li>
        <span class="icon">
          <svg width="14" height="14" viewBox="0 0 24 24" aria-hidden="true"><rect x="2" y="5" width="20" height="14" rx="1.5" fill="#fff"/><path d="M3 6l9 7 9-7" stroke="#1a5a74" stroke-width="1.8" fill="none"/></svg>
        </span>
        hlelectricalsolutions@mailvento.com
      </li>
    </ul>
    <div class="social">
      <span class="social__mark" aria-hidden="true"></span>
      <span class="social__mark" aria-hidden="true"></span>
      <span class="social__handle">@hlelectricalsolutions</span>
    </div>
    <div class="card__band"></div>
  </section>

</body>
</html>
```